Marlowe Hullcraft

Creating a brochure for company that manufactures boats. 8x11
Cover: Black w/boat pictures (just the boat, not the background)
1st inside page: Maybe a gray background of some sort (fade).
2nd inside page:same
Back Cover: Black background

Please feel free to ask questions. Photos on the design have the name of the pic.

Target Market(s)

- Companies that sell boats
- Individuals looking for a new boat

Industry/Entity Type

It Company

Requirements
Must have
• The brochure must have 4 pages and use all of the photos provided in the slots notes on the handwritten design idea.

```html
<!DOCTYPE html>
<html lang="en">
<head>
<meta charset="utf-8">
<title>Marlowe Hullcraft – Standards, Options &amp; Features</title>
<link href="https://fonts.googleapis.com/css2?family=PT+Sans+Narrow:wght@400;700&family=Cinzel:wght@600;700&family=Open+Sans:wght@600&display=swap" rel="stylesheet">
<style>
  :root{
    --stage:#ececec;
    --night:#05070f;
    --deep:#0a1a3c;
    --ocean:#1d6db0;
    --sky:#3f93cf;
    --header:#3eb6e0;
    --row-tint:#e2f0fa;
    --row-plain:#ffffff;
    --rule:#b9cfe0;
    --ink:#1d2733;
    --white:#ffffff;
    --silver:#c9ccd2;
  }
  *{box-sizing:border-box;margin:0;padding:0}
  html,body{width:1200px;height:1000px;overflow:hidden;background:var(--stage)}
  .sheet{
    position:absolute;left:272px;top:50px;width:655px;height:900px;
    background:linear-gradient(180deg,var(--night) 0,var(--night) 32px,var(--sky) 40px,var(--ocean) 150px,#114e8c 330px,var(--deep) 620px,var(--night) 900px);
    box-shadow:0 2px 10px rgba(0,0,0,.25);
    overflow:hidden;
  }
  .top-rule{position:absolute;left:0;right:0;top:30px;height:3px;background:linear-gradient(90deg,#555,#ddd 50%,#555)}
  .badge{position:absolute;left:205px;top:35px;width:245px;height:58px}
  .brand{
    position:absolute;left:205px;top:52px;width:245px;text-align:center;
    font-family:"Cinzel",serif;font-weight:700;font-size:19px;letter-spacing:1px;color:var(--silver);
  }
  .title{
    position:absolute;left:0;right:0;top:101px;text-align:center;
    font-family:"Cinzel",serif;font-weight:600;font-size:14px;letter-spacing:2.5px;color:var(--white);
  }
  .boat{position:absolute;top:125px;height:30px;border-radius:3px;background:linear-gradient(180deg,#d9e6ef,#8fb3c9)}
  .boat-a{left:325px;width:75px}
  .boat-b{left:405px;width:70px;top:130px;height:25px}
  .boat-c{left:495px;width:90px}
  .specs{position:absolute;left:65px;top:155px;width:524px;border-collapse:collapse;font-family:"PT Sans Narrow",sans-serif;font-size:11px;color:var(--ink);box-shadow:0 0 14px rgba(0,0,0,.5)}
  .specs th{background:var(--header);color:var(--white);height:16px;font-weight:700;text-align:center;font-family:"Cinzel",serif;font-size:10px;letter-spacing:.5px}
  .specs th.feature-head{text-align:left;padding-left:4px;font-family:"PT Sans Narrow",sans-serif;font-size:12.5px}
  .specs td{height:16.27px;border:1px solid var(--rule);text-align:center;line-height:1}
  .specs td:first-child{text-align:left;padding-left:4px;width:230px}
  .specs td:not(:first-child){width:98px}
  .specs tbody tr:nth-child(odd){background:var(--row-tint)}
  .specs tbody tr:nth-child(even){background:var(--row-plain)}
  .web{position:absolute;left:0;right:0;top:854px;text-align:center;font-family:"Open Sans",sans-serif;font-weight:600;font-size:14px;color:var(--white)}
</style>
</head>
<body>
<main class="sheet">
  <div class="top-rule"></div>
  <svg class="badge" viewBox="0 0 245 58" aria-hidden="true"><polygon points="0,0 245,0 228,58 17,58" fill="#0b0d12" stroke="#6b7079" stroke-width="1.5"/></svg>
  <div class="brand">Marlowe Hullcraft</div>
  <h1 class="title">Standards, options &amp; features</h1>
  <div class="boat boat-a" role="img" aria-label="220 Bay boat photo"></div>
  <div class="boat boat-b" role="img" aria-label="260 Bay boat photo"></div>
  <div class="boat boat-c" role="img" aria-label="262 CC boat photo"></div>
  <table class="specs">
    <thead><tr><th class="feature-head">STANDARD FEATURES</th><th>220 Bay</th><th>260 Bay</th><th>262 CC</th></tr></thead>
    <tbody>
      <tr><td>Jack Plate - Hydraulic</td><td>S</td><td>S</td><td>N/A</td></tr>
      <tr><td>Cushions - Removable Bow</td><td>O</td><td>O</td><td>S</td></tr>
      <tr><td>Seat - Cooler Seat with Backrest - Forward of Console</td><td>S</td><td>S</td><td>S</td></tr>
      <tr><td>Battery Compartment</td><td>S</td><td>S</td><td>S</td></tr>
      <tr><td>Livewells - Transom Bait Station</td><td>S</td><td>S</td><td>S</td></tr>
      <tr><td>Automatic Bilge Pump</td><td>S</td><td>S</td><td>S</td></tr>
      <tr><td>Compass</td><td>S</td><td>S</td><td>S</td></tr>
      <tr><td>Washdown - Fresh Water</td><td>O</td><td>O</td><td>O</td></tr>
      <tr><td>Washdown - Raw Water</td><td>O</td><td>O</td><td>O</td></tr>
      <tr><td>Lights - Navigation</td><td>S</td><td>S</td><td>S</td></tr>
      <tr><td>Pop Up Cleats - Stainless Steel</td><td>S</td><td>S</td><td>S</td></tr>
      <tr><td>Stainless Steel Cleats</td><td>O</td><td>O</td><td>O</td></tr>
      <tr><td>Switch Panel w/ Breakers - Water Resistant</td><td>S</td><td>S</td><td>S</td></tr>
      <tr><td>Stainless Bow and Stern Eyes</td><td>S</td><td>S</td><td>S</td></tr>
      <tr><td>Stainless Steering Wheel</td><td>S</td><td>S</td><td>S</td></tr>
      <tr><td>Vacuum Bagged Hull</td><td>S</td><td>S</td><td>S</td></tr>
      <tr><td>Bow Casting Platform with Storage</td><td>S</td><td>S</td><td>S</td></tr>
      <tr><td>Hydraulic Steering</td><td>O</td><td>O</td><td>S</td></tr>
      <tr><td>Stern Casting Platform</td><td>S</td><td>S</td><td>N/A</td></tr>
      <tr><td>Anchor Storage</td><td>S</td><td>S</td><td>S</td></tr>
      <tr><td>Tackle Station - Integrated in Helm Seat</td><td>S</td><td>S</td><td>S</td></tr>
      <tr><td>Drink Holders</td><td>S (2)</td><td>S (4)</td><td>S (6)</td></tr>
      <tr><td>Cushions - Aft Seat(s)</td><td>S</td><td>S</td><td>S</td></tr>
      <tr><td>Head - Enclosed Porcelain AquaFlush</td><td>N/A</td><td>N/A</td><td>S</td></tr>
      <tr><td>Rod Holders - GunwaleMount (6)</td><td>S (4)</td><td>S (6)</td><td>S (6)</td></tr>
      <tr><td>Steering - Tilt</td><td>S</td><td>S</td><td>S</td></tr>
      <tr><td>GPS Chart Plotter</td><td>O</td><td>O</td><td>O</td></tr>
      <tr><td>Rub Rail - Upgraded Stainless Steel Insert</td><td>S</td><td>S</td><td>S</td></tr>
      <tr><td>Stereo - Harbor Audio - 4 Speakers - MP3 - 12 V Adapter</td><td>S</td><td>S</td><td>S</td></tr>
      <tr><td>Stereo Upgrade - Subwoofer - Power Amp</td><td>O</td><td>O</td><td>O</td></tr>
      <tr><td>Trim Tabs</td><td>O</td><td>O</td><td>O</td></tr>
      <tr><td>Lockable Console Storage</td><td>S</td><td>S</td><td>S</td></tr>
      <tr><td>Prop(s) -Tidewell PowerMatched - Stainless Steel</td><td>S</td><td>S</td><td>S</td></tr>
      <tr><td>Top - Bimini Top - ColorMatched</td><td>O</td><td>O</td><td>O</td></tr>
      <tr><td>Top - T-Top with Canvas</td><td>O</td><td>O</td><td>N/A</td></tr>
      <tr><td>T-Top with Hard Top - Custom Design with “M” Logo</td><td>N/A</td><td>N/A</td><td>S</td></tr>
      <tr><td>Rod Holders - T-Top</td><td>N/A</td><td>N/A</td><td>S</td></tr>
      <tr><td>Lights - Cockpit (2)</td><td>S</td><td>S</td><td>S</td></tr>
      <tr><td>Warranty - Limited Lifetime</td><td>S</td><td>S</td><td>S</td></tr>
      <tr><td>Ladder - Dive / Swim Ladder</td><td>O</td><td>O</td><td>S</td></tr>
      <tr><td>Seats - Helm - Upgraded with Flip Up Bolsters</td><td>S</td><td>S</td><td>S</td></tr>
    </tbody>
  </table>
  <p class="web">www.marlowehullcraft.com</p>
</main>
</body>
</html>
```